Oil Field Service company needs professional business cards

Looking to clean up our current company business cards and look a little more professional. Brenwick Casing Services is a US based company that services the oil field. We deal with engineers, managers and oil rigs....................................................................................................................................................................................................................................................................................................................................................................................................

Target Market(s)

Oil and Gas professionals

Industry/Entity Type

Oil And Gas

Contact Information for Business Card

See attached photo as example

Font styles to use
Sans Serif

Colors
ec1f27

Requirements
Must have
• Company Logo, Name, Title, Cell, Office, Fax, Email.
• See attached photo
Nice to have
• External CRT, Internal CRT, Casing Crews, Torque Turn, Laydown Machine
Should not have
• Do not introduce any new pictures and keep it professional looking

```html
<!DOCTYPE html>
<html lang="en">
<head>
<meta charset="utf-8">
<title>Brenwick Casing Services – Business Card</title>
<link href="https://fonts.googleapis.com/css2?family=Roboto:wght@400;500;700&family=Roboto+Condensed:wght@400&display=swap" rel="stylesheet">
<style>
  :root {
    --red: #ec1f27;
    --navy: #3b4e61;
    --ink: #3a3a3a;
    --card: #f7f7f7;
    --backdrop: #e6e6e6;
  }
  * { margin: 0; padding: 0; box-sizing: border-box; }
  html, body { width: 1200px; height: 576px; overflow: hidden; }
  body {
    background: var(--backdrop);
    font-family: "Roboto", Arial, sans-serif;
    position: relative;
  }
  .card {
    position: absolute;
    width: 482px;
    height: 292px;
    background: var(--card);
    border-radius: 6px;
    box-shadow: 0 2px 4px rgba(0,0,0,.18);
    overflow: hidden;
  }
  .card-front { left: 82px; top: 140px; }
  .card-back { left: 602px; top: 138px; }

  .wordmark {
    color: var(--navy);
    font-weight: 700;
    text-align: center;
    line-height: 1;
  }
  .wordmark-name { display: block; letter-spacing: 1px; }
  .wordmark-tagline { display: block; letter-spacing: 3px; }

  .card-front .wordmark {
    position: absolute; left: 0; right: 0; top: 78px;
  }
  .card-front .wordmark-name { font-size: 50px; }
  .card-front .wordmark-tagline { font-size: 17px; margin-top: 22px; }

  .service-band {
    position: absolute; left: 0; right: 0; top: 219px; height: 27px;
    background: var(--red);
    color: #fff;
    font-weight: 500;
    font-size: 13px;
    display: flex; align-items: center; justify-content: center; gap: 7px;
    letter-spacing: .2px;
  }
  .service-band .divider { font-weight: 400; }

  .web-line {
    position: absolute; left: 0; right: 0; top: 259px;
    display: flex; align-items: center; justify-content: center; gap: 10px;
    font-size: 13px; color: var(--ink);
  }
  .web-line .rule { width: 66px; height: 2px; background: var(--red); }

  .name-accent {
    position: absolute; left: 0; top: 34px; width: 13px; height: 48px;
    background: var(--red);
  }
  .holder { position: absolute; left: 28px; top: 36px; }
  .holder-name {
    font-family: "Roboto Condensed", Arial, sans-serif;
    font-size: 23px; color: var(--ink); line-height: 1.1;
  }
  .holder-title { font-size: 11.5px; color: var(--ink); margin-top: 3px; }

  .card-back .wordmark {
    position: absolute; left: 238px; width: 226px; top: 46px;
  }
  .card-back .wordmark-name { font-size: 30px; }
  .card-back .wordmark-tagline { font-size: 11px; margin-top: 12px; letter-spacing: 2px; }

  .contact-list {
    position: absolute; left: 28px; top: 181px;
    list-style: none;
    font-size: 11.5px; color: var(--ink);
  }
  .contact-list li { display: flex; align-items: center; gap: 8px; height: 16.2px; }
  .contact-list svg { width: 10px; height: 10px; fill: var(--red); flex: none; }
</style>
</head>
<body>

<section class="card card-front">
  <div class="wordmark">
    <span class="wordmark-name">BRENWICK</span>
    <span class="wordmark-tagline">CASING SERVICES</span>
  </div>
  <div class="service-band">
    <span>LAYDOWN MACHINE</span><span class="divider">|</span>
    <span>CASING CREW</span><span class="divider">|</span>
    <span>MUD TOOL</span><span class="divider">|</span>
    <span>TORQUE TURN</span>
  </div>
  <div class="web-line">
    <span class="rule"></span>
    <span>www.brenwickcs.com</span>
    <span class="rule"></span>
  </div>
</section>

<section class="card card-back">
  <span class="name-accent"></span>
  <div class="holder">
    <p class="holder-name">Cody Harlan</p>
    <p class="holder-title">Area Manager</p>
  </div>
  <div class="wordmark">
    <span class="wordmark-name">BRENWICK</span>
    <span class="wordmark-tagline">CASING SERVICES</span>
  </div>
  <ul class="contact-list">
    <li><svg viewBox="0 0 10 10" aria-hidden="true"><path d="M2 0.5l1.6 2-1 1a5 5 0 0 0 3.9 3.9l1-1 2 1.6-1 1.5C4.5 9.5.5 5.5.5 1.5z"/></svg>(580) 555-0142</li>
    <li><svg viewBox="0 0 10 10" aria-hidden="true"><path d="M0.5 3.5C2 1.5 8 1.5 9.5 3.5v1.2H7.2V3.6H2.8v1.1H.5z"/><rect x="1.5" y="5.3" width="7" height="4" rx="0.8"/></svg>(580) 555-0187</li>
    <li><svg viewBox="0 0 10 10" aria-hidden="true"><rect x="2.5" y="0.5" width="5" height="3"/><rect x="0.5" y="3.8" width="9" height="4" rx="0.6"/><rect x="2.5" y="7" width="5" height="2.5"/></svg>(580) 555-0163</li>
    <li><svg viewBox="0 0 10 10" aria-hidden="true"><path d="M5 0.3a3.5 3.5 0 0 0-3.5 3.5C1.5 6.5 5 9.7 5 9.7s3.5-3.2 3.5-5.9A3.5 3.5 0 0 0 5 .3zm0 5a1.4 1.4 0 1 1 0-2.8 1.4 1.4 0 0 1 0 2.8z"/></svg>Redfield, OK 73840</li>
    <li><svg viewBox="0 0 10 10" aria-hidden="true"><path d="M0.5 2h9v.6L5 5.5.5 2.6z"/><path d="M0.5 3.5L5 6.4l4.5-2.9V8h-9z"/></svg>codyharlan@brenwickcs.com</li>
    <li><svg viewBox="0 0 10 10" aria-hidden="true"><circle cx="5" cy="5" r="4.5"/><path d="M0.8 5h8.4M5 .6c-2 2.6-2 6.2 0 8.8M5 .6c2 2.6 2 6.2 0 8.8" stroke="#f7f7f7" stroke-width="0.8" fill="none"/></svg>www.brenwickcs.com</li>
  </ul>
</section>

</body>
</html>
```